Brightfen Business Card Redesign & Logo Update

We need to update our business cards to something more modern and fresh. Brightfen can provide the current color schemes and old design examples, but welcome creativity in helping us with this redesign. PLEASE NOTE that we no longer utilize the "tree" and/or "leaf" imagery in our branding. If able would apprecaite an update on the quality of our "words only" logo in Ai. / PNG formats too.

Target Market(s)

Investors, landowners, corporate partners, contractors

Industry/Entity Type

Environmental Restoration & Conservation

Contact Information for Business Card

Logo, persons name, title, mailing address, phone and email, website url

Font styles to use
Other font styles liked:
• Merriweather

Requirements
Nice to have
• Logo, persons name, title, mailing address, phone and email, website url, but open to ideams
Should not have
• No all back backgrounds

```html
<!DOCTYPE html>
<html lang="en">
<head>
<meta charset="utf-8">
<title>Brightfen Business Card</title>
<link rel="stylesheet" href="https://fonts.googleapis.com/css2?family=Merriweather:wght@300;400;700;900&display=swap">
<style>
  :root {
    --backdrop: #9a9a9a;
    --card: #ffffff;
    --green: #157a3b;
    --orange: #ec7a23;
    --ink: #1a1a1a;
    --text: #3b3b3b;
  }
  * { margin: 0; padding: 0; box-sizing: border-box; }
  html, body {
    width: 1049px; height: 1200px; overflow: hidden;
    background: var(--backdrop);
    font-family: "Merriweather", Georgia, serif;
  }
  .canvas { position: relative; width: 1049px; height: 1200px; }
  .card {
    position: absolute; left: 163px; width: 723px; height: 413px;
    background: var(--card); border-radius: 26px; overflow: hidden;
  }
  .card--front { top: 140px; }
  .card--back { top: 646px; }

  .wordmark { position: absolute; text-align: center; }
  .wordmark__name {
    display: block; font-weight: 900; color: var(--green);
    letter-spacing: 1px; line-height: 1;
  }
  .wordmark__tagline {
    display: block; font-weight: 700; color: var(--ink);
    text-transform: uppercase; line-height: 1; white-space: nowrap;
  }
  .card--front .wordmark { left: 0; right: 0; top: 178px; }
  .card--front .wordmark__name { font-size: 66px; }
  .card--front .wordmark__tagline { font-size: 19.5px; margin-top: 14px; letter-spacing: 0.2px; }

  .card--back .wordmark { left: 398px; width: 286px; top: 50px; }
  .card--back .wordmark__name { font-size: 38px; }
  .card--back .wordmark__tagline { font-size: 11.8px; margin-top: 10px; }

  .edge-band { position: absolute; left: 0; top: 0; width: 16px; height: 413px; }

  .person { position: absolute; left: 39px; top: 178px; }
  .person__name { font-size: 26px; font-weight: 700; color: var(--green); line-height: 1.2; }
  .person__title { font-size: 19px; font-weight: 400; color: var(--orange); margin-top: 2px; }

  .address {
    position: absolute; left: 407px; top: 180px;
    font-size: 19px; font-weight: 300; color: var(--text); line-height: 29px;
  }
  .contacts { position: absolute; left: 412px; top: 285px; list-style: none; }
  .contacts__item {
    display: flex; align-items: center; height: 28.5px;
    font-size: 19px; font-weight: 300; color: var(--text);
  }
  .contacts__icon { width: 16px; height: 16px; margin-right: 7px; flex: none; }
</style>
</head>
<body>
<main class="canvas">
  <section class="card card--front" aria-label="Card front">
    <div class="wordmark">
      <span class="wordmark__name">BRIGHTFEN</span>
      <span class="wordmark__tagline">Environmental Credit Company</span>
    </div>
  </section>

  <section class="card card--back" aria-label="Card back">
    <svg class="edge-band" viewBox="0 0 16 413" aria-hidden="true">
      <path d="M0 0 H16 V170 Q16 176 10 176 H0 Z" fill="var(--green)"/>
      <rect x="-8" y="180" width="24" height="50" rx="6" fill="var(--orange)"/>
      <path d="M0 234 H10 Q16 234 16 240 V413 H0 Z" fill="var(--green)"/>
    </svg>

    <div class="wordmark">
      <span class="wordmark__name">BRIGHTFEN</span>
      <span class="wordmark__tagline">Environmental Credit Company</span>
    </div>

    <div class="person">
      <p class="person__name">DANA WHITLOCK</p>
      <p class="person__title">President</p>
    </div>

    <address class="address" style="font-style: normal;">
      1870 Larkspur Cove Dr<br>
      Larkspur Bay CA 90417
    </address>

    <ul class="contacts">
      <li class="contacts__item">
        <svg class="contacts__icon" viewBox="0 0 16 16" aria-hidden="true">
          <path d="M4 1.5 L6.2 4.6 L4.8 6.2 Q6.2 9 9.8 11.2 L11.4 9.8 L14.5 12 L13 14.5 Q7 14 3.3 9.5 Q1 6 1.5 3.2 Z" fill="var(--orange)"/>
        </svg>
        555-318-2047
      </li>
      <li class="contacts__item">
        <svg class="contacts__icon" viewBox="0 0 16 16" aria-hidden="true">
          <rect x="1.5" y="4" width="13" height="9" rx="1" fill="var(--orange)"/>
          <path d="M1.8 4.5 L8 9 L14.2 4.5" stroke="#fff" stroke-width="1.2" fill="none"/>
        </svg>
        dwhitlock@brightfen.com
      </li>
      <li class="contacts__item">
        <svg class="contacts__icon" viewBox="0 0 16 16" aria-hidden="true">
          <circle cx="8" cy="8" r="6.5" fill="var(--orange)"/>
          <ellipse cx="8" cy="8" rx="2.6" ry="6.5" fill="none" stroke="#fff" stroke-width="1"/>
          <line x1="1.5" y1="8" x2="14.5" y2="8" stroke="#fff" stroke-width="1"/>
        </svg>
        www.brightfen.com
      </li>
    </ul>
  </section>
</main>
</body>
</html>
```